tallow-brook.com

We are a small dollar lending company that will revolutionize the industry. We will do this by being completely transparent, fee free, etc and an interest rate that normal people can afford to pay. Over 10X less than our competition. We only allow our members to pay bills " bills paid fast", within 72 hours. Payday loans typically charge from 390%-600% with a terrible payback structure. We charge 36%, period, with a payback structure over 12 months. Our site will be very simple and easy to use but elegant at the same time. We do not want the site to be too busy, less is more and easier. We will have; Home, The Story, Why tallowbrook.com, Are you eligible? Members, Clients. To become a member you have to be referred by a current client of tallowbrook.com. A lot of the busy stuff will be saved for the Members and Clients sections. The feel must be elegant, easy to use and very simple to understand. I am looking for the green, white and black combinations of colors, very similar to my logo that was designed by Fernquillo.

```html
<!DOCTYPE html>
<html lang="en">
<head>
<meta charset="utf-8">
<title>Tallow Brook – A Licensed Money Lender</title>
<link rel="stylesheet" href="https://fonts.googleapis.com/css2?family=Open+Sans:wght@400;600;700&display=swap">
<style>
  :root {
    --green: #8cc540;
    --green-dark: #7fb637;
    --green-pale: #d9ecbf;
    --charcoal: #3f3f3f;
    --nav-top: #4a4a4a;
    --nav-bottom: #333333;
    --hero-bg: #f6f6f6;
    --panel-grey: #efefef;
    --ink: #222222;
    --white: #ffffff;
    --frame: #dddddd;
  }
  * { box-sizing: border-box; margin: 0; padding: 0; }
  html, body { width: 1050px; height: 1200px; overflow: hidden; }
  body { position: relative; background: var(--white); font-family: "Open Sans", Arial, sans-serif; color: var(--ink); }
  .abs { position: absolute; }

  /* Header */
  .site-header { left: 0; top: 0; width: 1050px; height: 102px; background: var(--green); }
  .brand { left: 152px; top: 34px; display: flex; align-items: center; gap: 8px; color: var(--white); font-weight: 600; font-size: 20px; letter-spacing: .3px; }
  .brand-dot { width: 26px; height: 26px; border: 4px solid var(--white); border-radius: 50%; }
  .contact { left: 760px; top: 30px; display: flex; gap: 14px; color: var(--white); }
  .contact svg { margin-top: 14px; }
  .contact-label { font-size: 15px; font-weight: 600; line-height: 22px; }
  .contact-phone { font-size: 13.5px; line-height: 20px; }

  /* Navigation */
  .main-nav { left: 0; top: 102px; width: 1050px; height: 48px; background: linear-gradient(var(--nav-top), var(--nav-bottom)); }
  .nav-list { left: 160px; top: 0; height: 48px; display: flex; list-style: none; }
  .nav-item { height: 48px; line-height: 48px; padding: 0 19px; color: var(--white); font-size: 11px; font-weight: 600; white-space: nowrap; border-right: 1px solid #2c2c2c; box-shadow: 1px 0 0 #555; }
  .nav-item:last-child { border-right: none; box-shadow: none; }
  .search { left: 732px; top: 12px; width: 129px; height: 24px; background: var(--white); border-radius: 4px; font-size: 9px; color: #555; line-height: 24px; padding-left: 13px; }
  .search-icon { left: 871px; top: 16px; }

  /* Hero */
  .hero { left: 0; top: 150px; width: 1050px; height: 400px; background: var(--hero-bg); border-bottom: 1px solid #e6e6e6; }
  .hero-photo { left: 151px; top: 168px; width: 301px; height: 382px; background: radial-gradient(ellipse at 55% 40%, #e8d6c6 0%, #e6e9dc 45%, var(--hero-bg) 80%); }
  .hero-title { left: 490px; top: 230px; color: var(--green); font-size: 35px; font-weight: 600; line-height: 57px; letter-spacing: .5px; }
  .hero-text { left: 490px; top: 357px; width: 412px; font-size: 10.6px; line-height: 16.5px; text-align: justify; color: #333; }
  .dot { top: 437px; width: 12px; height: 12px; border-radius: 50%; background: #333; border: 2px solid #e2e2e2; }
  .dot.active { background: var(--green); }

  /* Features */
  .features { left: 151px; top: 579px; width: 750px; height: 183px; background: var(--green); box-shadow: 0 8px 10px -6px rgba(0,0,0,.18); display: flex; }
  .feature { position: relative; text-align: center; color: var(--white); border-right: 1px solid var(--green-dark); }
  .feature:last-child { border-right: none; }
  .feature-icon { margin: 19px auto 0; width: 100px; height: 100px; border-radius: 50%; background: #f1f1f1; border: 5px solid var(--white); display: flex; align-items: center; justify-content: center; }
  .feature-title { margin-top: 12px; font-size: 13.5px; text-transform: uppercase; }
  .feature-sub { margin-top: 3px; font-size: 11px; }

  /* Content columns */
  .photo-frame { top: 795px; width: 234px; height: 157px; border: 1px solid var(--frame); padding: 3px; background: var(--white); }
  .photo-fill { width: 100%; height: 100%; }
  .col-title { top: 962px; font-size: 16px; font-weight: 400; }
  .col-title span { color: var(--green); font-weight: 600; }
  .col-text { top: 992px; width: 234px; font-size: 9.5px; line-height: 16.5px; text-align: justify; color: #333; }

  .promo { left: 664px; top: 795px; width: 237px; height: 290px; }
  .promo-text { height: 173px; background: var(--panel-grey); color: var(--green); font-size: 19px; font-weight: 600; line-height: 31.5px; text-align: center; padding: 10px 20px 0; }
  .promo-badge { height: 117px; background: var(--green); display: flex; align-items: center; justify-content: center; }
  .badge-placeholder { width: 84px; height: 84px; border-radius: 50%; background: var(--green-pale); }

  /* Footer */
  .site-footer { left: 0; top: 1118px; width: 1050px; height: 82px; background: var(--charcoal); border-top: 3px solid var(--green); }
  .footer-links { left: 152px; top: 20px; color: var(--white); font-size: 9.5px; }
  .footer-links .sep { margin: 0 5px; }
  .copyright { left: 151px; top: 48px; color: #dcdcdc; font-size: 9.5px; }
  .social { left: 720px; top: 30px; display: flex; gap: 8px; }
  .social span { width: 18px; height: 18px; border-radius: 50%; background: var(--white); }
</style>
</head>
<body>

<header class="site-header abs">
  <div class="brand abs"><span class="brand-dot"></span>TALLOW BROOK</div>
  <div class="contact abs">
    <svg width="22" height="20" viewBox="0 0 22 20" aria-hidden="true">
      <path d="M1 7 Q11 -1 21 7 L18 10 L15 7 L7 7 L4 10 Z" fill="#111"/>
      <rect x="4" y="9" width="14" height="10" rx="2" fill="#111"/>
      <g fill="#8cc540"><rect x="7" y="12" width="2" height="2"/><rect x="10" y="12" width="2" height="2"/><rect x="13" y="12" width="2" height="2"/><rect x="7" y="15" width="2" height="2"/><rect x="10" y="15" width="2" height="2"/><rect x="13" y="15" width="2" height="2"/></g>
    </svg>
    <div>
      <div class="contact-label">Call For Info</div>
      <div class="contact-phone">+1-555-014-2270</div>
    </div>
  </div>
</header>

<nav class="main-nav abs">
  <ul class="nav-list abs">
    <li class="nav-item">Home</li>
    <li class="nav-item">The Story</li>
    <li class="nav-item">Why tallowbrook.com</li>
    <li class="nav-item">Are you eligible? Members</li>
    <li class="nav-item">Clients</li>
  </ul>
  <div class="search abs">Search</div>
  <svg class="search-icon abs" width="15" height="15" viewBox="0 0 15 15" aria-hidden="true">
    <circle cx="6" cy="6" r="4.5" fill="none" stroke="#e8e8d8" stroke-width="2"/>
    <line x1="9.5" y1="9.5" x2="14" y2="14" stroke="#e8e8d8" stroke-width="2.5" stroke-linecap="round"/>
  </svg>
</nav>

<section class="hero abs"></section>
<div class="hero-photo abs" role="img" aria-label="Smiling woman holding banknotes beside a pink piggy bank"></div>
<h1 class="hero-title abs">A LICENSED<br>MONEY LENDER</h1>
<p class="hero-text abs">We are a small dollar lending company, We will do this by being completely transparent, fee free, etc and an interest rate that normal people can afford to pay. Over 10X less than our competition.</p>
<span class="dot active abs" style="left:491px"></span>
<span class="dot abs" style="left:508px"></span>
<span class="dot abs" style="left:525px"></span>

<section class="features abs">
  <div class="feature" style="width:242px">
    <div class="feature-icon">
      <svg width="50" height="50" viewBox="0 0 50 50" aria-hidden="true">
        <circle cx="25" cy="25" r="20" fill="none" stroke="#111" stroke-width="3"/>
        <path d="M15 27 A10 10 0 0 1 33 19" fill="none" stroke="#111" stroke-width="4"/>
        <path d="M30 14 L37 18 L31 23 Z" fill="#111"/>
        <path d="M35 23 A10 10 0 0 1 17 31" fill="none" stroke="#111" stroke-width="4"/>
        <path d="M20 36 L13 32 L19 27 Z" fill="#111"/>
      </svg>
    </div>
    <div class="feature-title">Completely Transparent</div>
    <div class="feature-sub">Small dollar lending company</div>
  </div>
  <div class="feature" style="width:263px">
    <div class="feature-icon">
      <svg width="52" height="52" viewBox="0 0 52 52" aria-hidden="true">
        <g fill="#111">
          <circle cx="15" cy="10" r="6"/><path d="M5 28 Q5 17 15 17 Q25 17 25 28 Z"/>
          <circle cx="37" cy="10" r="6"/><path d="M27 28 Q27 17 37 17 Q47 17 47 28 Z"/>
          <circle cx="26" cy="27" r="6.5" stroke="#f1f1f1" stroke-width="2"/><path d="M14 48 Q14 35 26 35 Q38 35 38 48 Z" stroke="#f1f1f1" stroke-width="2"/>
        </g>
      </svg>
    </div>
    <div class="feature-title">Are You Eligible? Members</div>
    <div class="feature-sub">Lorem ipsum dolor sit amet</div>
  </div>
  <div class="feature" style="width:245px">
    <div class="feature-icon">
      <svg width="52" height="52" viewBox="0 0 52 52" aria-hidden="true">
        <path d="M34 8 L48 4" stroke="#111" stroke-width="4" stroke-linecap="round"/>
        <path d="M3 14 L36 14 L31 34 L12 34 Z" fill="#111"/>
        <path d="M36 10 L30 38 L12 38" fill="none" stroke="#111" stroke-width="3"/>
        <circle cx="15" cy="44" r="3.5" fill="#111"/><circle cx="28" cy="44" r="3.5" fill="#111"/>
      </svg>
    </div>
    <div class="feature-title">Pay Bills</div>
    <div class="feature-sub">Lorem ipsum dolor sit amet</div>
  </div>
</section>

<div class="photo-frame abs" style="left:151px">
  <div class="photo-fill" role="img" aria-label="Customer service agent with headset in a bright office" style="background:linear-gradient(90deg,#c9c3bb,#e2e0dc 45%,#6b6664 80%,#b7b2ab)"></div>
</div>
<h2 class="col-title abs" style="left:150px">Welcome To <span>Tallow Brook</span></h2>
<p class="col-text abs" style="left:151px">Lorem ipsum dolor sit amet, consectetur adipisc elit. Proin ultricies vestibulum velit, bibendum et condimentum metusip dolore ipsum. Lorem ipsum dolor sit amet, consectetur adipisc elit. Proin ultricies vestibulum velit, bibendum et condimentum metusip dolore ipsum.</p>

<div class="photo-frame abs" style="left:408px">
  <div class="photo-fill" role="img" aria-label="Business colleagues giving a high five across a desk" style="background:linear-gradient(135deg,#b9b8b4,#dedcd8 50%,#e9d9cc 75%,#c8c6c2)"></div>
</div>
<h2 class="col-title abs" style="left:407px">The Story</h2>
<p class="col-text abs" style="left:408px">Lorem ipsum dolor sit amet, consectetur adipisc elit. Proin ultricies vestibulum velit, bibendum et condimentum metusip dolore ipsum. Lorem ipsum dolor sit amet, consectetur adipisc elit. Proin ultricies vestibulum velit, bibendum et condimentum metusip dolore ipsum.</p>

<aside class="promo abs">
  <div class="promo-text">We charge only 36% and give over 12 months time to pay back, no fees, hidden costs etc.</div>
  <div class="promo-badge">
    <div class="badge-placeholder" role="img" aria-label="Guarantee badge"></div>
  </div>
</aside>

<footer class="site-footer abs">
  <div class="footer-links abs">Home<span class="sep">|</span>The Story<span class="sep">|</span>Why tallowbrook.com<span class="sep">|</span>Contact Us</div>
  <div class="copyright abs">©2014 tallow-brook.com, All Rights Reserved.</div>
  <div class="social abs"><span></span><span></span><span></span><span></span></div>
</footer>

</body>
</html>
```